Halvorsen Books & Consulting Brochure

I need a double sided brochure for a small business bookkeeping & consulting firm.

Halvorsen Books & Consulting (I have attached the Logo)

The brochure will be printed on 8.5" x 5.5" paper (Tib).

I'd like to use blues, whites and black colors...

The final product needs to communicate security, professional and current (not futuristic or dated).

I wouldn't mind a picture on 1 of the sides (professional person, a professional meeting, something along those lines).

I am visioning the brochure having 4 sections (2 on front and 2 on back)

Section 1 - Why Outsource Bookkeeping?
Section 2 - Our Philosophy
Section 3 - Services
Section 4 - TBD

I'd like a shell to review before deciding on all of the wording. Some wording is below:

Why Outsource Bookkeeping?

More Time to Focus on your core business
2) Save Money – No More: payroll taxes, workers compensation, benefits, vacation, sick days, office space, hardware, technology, training, turnover…
3) Expertise – you have full time access to a highly skilled team at the cost of a paying a part time bookkeeper.
4) Focused Staff – no more office distractions. Having a remote bookkeeper allows you to focus on your business and allows them to focus on your financials.
5) Access to Top Technology Systems –outsourcing gives you access to the top tool in the industry. You don’t have the time to research and learn about the best financial tools for your business – let an expert handle that
6) Experience – an outsourced bookkeeper can share relevant knowledge gained from experience with other clients

Services:
Bookkeeping Controller Services Accounts Payable Management
Account Receivable Management Check Writing Account Reconciliations
Benchmarking Budgeting Financial Reports
Financial Consulting Profit and Growth Consulting Financial Planning
Succession & Exit Planning Electronic Filing Cabinet Marketing Consulting

Our Philosophy:

Accuracy – having strong financial systems in place that collect and measure all relevant data creates a compliant business and gives you a better understanding of your business.
Understanding – Understanding what financial data is important and what it really means for your business will allow you to take appropriate actions to grow your business or to prevent future issues.
Action – data in meaningless without action, however the right actions put you in control
Control – When you take action based on accurate data that you understand, you are in complete control of your business and its future.

Industry/Entity Type

Small Business

```html
<!DOCTYPE html>
<html lang="en">
<head>
<meta charset="utf-8">
<title>Halvorsen Books &amp; Consulting – Brochure</title>
<link rel="stylesheet" href="https://fonts.googleapis.com/css2?family=Lora:wght@400&family=Roboto+Condensed:wght@400;700&family=Open+Sans:ital,wght@0,400;0,600;0,700;1,400;1,600&family=Arimo:wght@400;700&display=swap">
<style>
:root{
  --sky:#29a3de;
  --sky-light:#3bb0e6;
  --royal:#1f74ba;
  --navy:#1a5f9e;
  --deep:#0f4f8a;
  --ink:#1a1a1a;
  --paper:#ffffff;
  --mist:#e9eaec;
  --fog:#d8dadd;
  --logo:#2a9bd6;
}
*{box-sizing:border-box;margin:0;padding:0}
html,body{width:1200px;height:848px;overflow:hidden;background:var(--paper)}
body{position:relative;font-family:"Open Sans",Arial,sans-serif;color:var(--ink)}
.page{position:absolute;width:510px;height:790px;overflow:hidden;box-shadow:0 2px 8px rgba(0,0,0,.25)}
.page--front{left:50px;top:21px;background:var(--sky)}
.page--back{left:625px;top:26px;background:var(--mist)}

/* front */
.brand-bar{position:absolute;left:12px;top:0;width:486px;height:72px;background:var(--paper);border-radius:0 0 12px 12px;display:flex;align-items:center;padding-left:16px;gap:14px}
.brand-mark{width:40px;height:40px;border-radius:50%;background:var(--logo)}
.brand-name{font-family:"Lora",Georgia,serif;font-size:28px;color:var(--logo);white-space:nowrap}
.cta-pill{position:absolute;left:26px;top:88px;width:458px;height:36px;background:var(--royal);border-radius:10px;color:#fff;font-family:"Roboto Condensed",Arial,sans-serif;font-weight:700;font-size:19px;display:flex;align-items:center;justify-content:center;letter-spacing:.3px}
.cta-pill::after{content:"";position:absolute;left:240px;bottom:-10px;border:8px solid transparent;border-top:10px solid var(--royal);border-bottom:0}
.phone-band{position:absolute;left:0;top:141px;width:510px;height:42px;background:var(--navy);display:flex;align-items:center;justify-content:center;gap:12px;color:#fff;font-family:"Arimo",Arial,sans-serif;font-weight:700;font-size:23px}
.phone-band svg{width:28px;height:28px}
.strengths{position:absolute;left:272px;top:190px;list-style:none}
.strengths li{display:flex;align-items:center;gap:10px;height:37px;font-family:"Open Sans",Arial,sans-serif;font-size:22px;color:#1d6cb3;opacity:.85}
.strengths svg{width:24px;height:24px}
.team-photo{position:absolute;left:0;top:298px;width:510px;height:240px;background:linear-gradient(135deg,#dfe8ef 0%,#b9c9d6 45%,#8aa2b6 75%,#5c7287 100%)}
.badge{position:absolute;left:18px;top:187px;width:176px;height:176px}
.benefits-tag{position:absolute;left:0;top:471px;width:272px;height:62px;background:rgba(31,116,186,.85);color:#fff;font-family:"Open Sans",Arial,sans-serif;font-size:17px;line-height:25px;padding:6px 0 0 26px;letter-spacing:.4px}
.services-head{position:absolute;left:0;top:540px;width:510px;height:37px;background:var(--royal);display:flex;align-items:center;justify-content:center;gap:14px;color:#fff;font-family:"Open Sans",Arial,sans-serif;font-weight:400;font-size:23px;letter-spacing:.5px}
.services-head i{display:block;width:62px;height:1px;background:#fff}
.services{position:absolute;top:590px;list-style:none;color:#fff;font-size:16.5px;line-height:22.5px;letter-spacing:.2px}
.services li::before{content:"• "}
.services--a{left:24px}
.services--b{left:262px}
.contact-band{position:absolute;left:0;top:732px;width:510px;height:58px;background:var(--royal);color:#fff;font-family:"Arimo",Arial,sans-serif;font-size:16px;line-height:20px}
.contact-band .icons{position:absolute;left:56px;top:9px;width:20px}
.contact-band .lines{position:absolute;left:92px;top:8px}
.contact-band .place{position:absolute;left:326px;top:8px}

/* back */
.back-top{position:absolute;left:0;top:0;width:510px;height:58px;background:var(--sky-light)}
.banner{position:absolute;left:0;height:44px;background:var(--royal);color:#fff;font-family:"Roboto Condensed",Arial,sans-serif;font-weight:700;font-size:25px;display:flex;align-items:center;padding-left:44px;clip-path:polygon(0 0,100% 0,calc(100% - 14px) 100%,0 100%)}
.banner::before{content:"";position:absolute;left:20px;top:14px;border-left:15px solid #fff;border-top:8px solid transparent;border-bottom:8px solid transparent}
.banner--why{top:9px;width:412px}
.banner--philo{top:445px;width:412px}
.chart-visual{position:absolute;left:0;top:62px;width:124px;height:372px;border:3px solid #1b1b1b;border-left:0;border-radius:0 14px 14px 0;background:linear-gradient(160deg,#eaf3fa 0%,#b6d3ea 40%,#6ea7d3 70%,#2f6fa8 100%)}
.reasons{position:absolute;left:137px;top:0;width:350px;list-style:none}
.reasons li{position:absolute;left:0;width:350px}
.reasons li:nth-child(1){top:74px}
.reasons li:nth-child(2){top:118px}
.reasons li:nth-child(3){top:196px}
.reasons li:nth-child(4){top:263px}
.reasons li:nth-child(5){top:326px}
.reasons li:nth-child(6){top:388px}
.reasons h3{font-family:"Arimo",Arial,sans-serif;font-weight:400;font-size:15.5px;color:var(--royal);line-height:18px}
.reasons h3::before{content:"";display:inline-block;margin-right:4px;border-left:9px solid var(--royal);border-top:5px solid transparent;border-bottom:5px solid transparent}
.reasons p{font-family:"Arimo",Arial,sans-serif;font-size:13.8px;line-height:17.5px;margin-left:-2px}
.philosophy{position:absolute;left:0;top:440px;width:510px;height:247px;background:var(--sky)}
.principles{position:absolute;left:0;top:493px;width:510px;list-style:none}
.principles li{position:relative;height:49px}
.principles .icon{position:absolute;left:3px;top:0;width:60px;height:44px;background:var(--royal);border-radius:6px;display:flex;align-items:center;justify-content:center}
.principles .icon svg{width:30px;height:30px}
.principles p{position:absolute;left:75px;top:4px;width:420px;color:#fff;font-size:14.2px;line-height:19px;font-style:italic;text-align:justify}
.principles li:last-child p{top:13px}
.principles b{font-style:normal;font-weight:700}
.cta-band{position:absolute;left:0;top:687px;width:510px;height:37px;background:var(--royal);color:#fff;font-family:"Roboto Condensed",Arial,sans-serif;font-weight:700;font-size:20px;display:flex;align-items:center;justify-content:center;letter-spacing:.3px}
.back-footer{position:absolute;left:0;top:724px;width:510px;height:66px;background:var(--mist);font-family:"Arimo",Arial,sans-serif;font-size:16px;line-height:24px}
.back-footer .mini-brand{position:absolute;left:16px;top:20px;display:flex;align-items:center;gap:8px;font-family:"Lora",Georgia,serif;font-size:22px;color:var(--logo)}
.back-footer .mini-brand span{width:24px;height:24px;border-radius:50%;background:var(--logo)}
.back-footer .lines{position:absolute;left:162px;top:8px}
.back-footer .lines div{display:flex;align-items:center;gap:10px}
.back-footer .lines svg{width:20px;height:20px}
.back-footer .place{position:absolute;left:400px;top:11px;line-height:20px}
</style>
</head>
<body>

<section class="page page--front">
  <header class="brand-bar">
    <span class="brand-mark"></span>
    <span class="brand-name">Halvorsen Books &amp; Consulting</span>
  </header>
  <div class="cta-pill">Schedule a Complimentary Consultation TODAY</div>
  <div class="phone-band">
    <svg viewBox="0 0 24 24"><path fill="#fff" d="M6.6 10.8c1.4 2.8 3.8 5.1 6.6 6.6l2.2-2.2c.3-.3.7-.4 1-.2 1.1.4 2.3.6 3.6.6.6 0 1 .4 1 1V20c0 .6-.4 1-1 1C10.6 21 3 13.4 3 4c0-.6.4-1 1-1h3.5c.6 0 1 .4 1 1 0 1.3.2 2.5.6 3.6.1.3 0 .7-.2 1z"/></svg>
    <span>484-555-0173</span>
    <svg viewBox="0 0 24 24"><path fill="#fff" d="M6.6 10.8c1.4 2.8 3.8 5.1 6.6 6.6l2.2-2.2c.3-.3.7-.4 1-.2 1.1.4 2.3.6 3.6.6.6 0 1 .4 1 1V20c0 .6-.4 1-1 1C10.6 21 3 13.4 3 4c0-.6.4-1 1-1h3.5c.6 0 1 .4 1 1 0 1.3.2 2.5.6 3.6.1.3 0 .7-.2 1z"/></svg>
  </div>
  <ul class="strengths">
    <li><svg viewBox="0 0 24 24"><rect x="2" y="4" width="18" height="18" rx="2" fill="none" stroke="#1d6cb3" stroke-width="2"/><path d="M6 12l4 5 11-14" fill="none" stroke="#1d6cb3" stroke-width="3"/></svg>Efficiency</li>
    <li><svg viewBox="0 0 24 24"><rect x="2" y="4" width="18" height="18" rx="2" fill="none" stroke="#1d6cb3" stroke-width="2"/><path d="M6 12l4 5 11-14" fill="none" stroke="#1d6cb3" stroke-width="3"/></svg>Experience</li>
    <li><svg viewBox="0 0 24 24"><rect x="2" y="4" width="18" height="18" rx="2" fill="none" stroke="#1d6cb3" stroke-width="2"/><path d="M6 12l4 5 11-14" fill="none" stroke="#1d6cb3" stroke-width="3"/></svg>Expertise</li>
  </ul>
  <div class="team-photo" role="img" aria-label="Photo of a smiling business team gathered around a laptop in a bright office"></div>
  <svg class="badge" viewBox="0 0 176 176" aria-label="Free initial consultation, no obligation">
    <g fill="#1f74ba" transform="translate(88 88)">
      <rect x="-66" y="-66" width="132" height="132"/>
      <rect x="-66" y="-66" width="132" height="132" transform="rotate(15)"/>
      <rect x="-66" y="-66" width="132" height="132" transform="rotate(30)"/>
      <rect x="-66" y="-66" width="132" height="132" transform="rotate(45)"/>
      <rect x="-66" y="-66" width="132" height="132" transform="rotate(60)"/>
      <rect x="-66" y="-66" width="132" height="132" transform="rotate(75)"/>
    </g>
    <circle cx="88" cy="88" r="74" fill="#1a5f9e" stroke="#fff" stroke-width="2"/>
    <line x1="26" y1="101" x2="150" y2="101" stroke="#fff" stroke-width="1.5"/>
    <g fill="#fff" font-family="Roboto Condensed, Arial, sans-serif" text-anchor="middle">
      <text x="88" y="60" font-size="24" font-weight="700">FREE</text>
      <text x="88" y="89" font-size="22" font-weight="700">Initial Consultation</text>
      <text x="88" y="130" font-size="22" font-weight="700">No obligation</text>
    </g>
  </svg>
  <div class="benefits-tag">Enjoy The Benefits of<br>Outsource BookKeeping</div>
  <h2 class="services-head"><i></i>SERVICES<i></i></h2>
  <ul class="services services--a">
    <li>Bookkeeping</li>
    <li>Controller Services</li>
    <li>A/P &amp; AR Management</li>
    <li>Check Writing</li>
    <li>Account Reconciliations</li>
    <li>Benchmarking Budgeting</li>
  </ul>
  <ul class="services services--b">
    <li>Financial Reports</li>
    <li>Financial Consulting</li>
    <li>Financial Planning</li>
    <li>Succession &amp; Exit Planning</li>
    <li>Electronic Filing Cabinet</li>
    <li>Marketing Consulting</li>
  </ul>
  <footer class="contact-band">
    <svg class="icons" viewBox="0 0 20 40"><circle cx="10" cy="9" r="7" fill="none" stroke="#9fd3f2" stroke-width="2"/><circle cx="10" cy="9" r="2.5" fill="#9fd3f2"/><rect x="2" y="25" width="16" height="11" fill="none" stroke="#9fd3f2" stroke-width="1.8"/><path d="M2 25l8 6 8-6" fill="none" stroke="#9fd3f2" stroke-width="1.8"/></svg>
    <div class="lines">484-555-0173<br>erik@halvorsenbooks.com</div>
    <div class="place">Maple Valley,<br>PA</div>
  </footer>
</section>

<section class="page page--back">
  <div class="back-top"></div>
  <h2 class="banner banner--why">Why Outsource BookKeeping?</h2>
  <div class="chart-visual" role="img" aria-label="Photo of a hand pointing at financial bar charts on a tablet"></div>
  <ul class="reasons">
    <li><h3>SAVE TIME</h3><p>Spend more time Focusing on your core business</p></li>
    <li><h3>SAVE MONEY</h3><p>No more payroll taxes, workers compensation,<br>benefits, vacation, sick days, office space, hardware,<br>technology, training &amp; turnover</p></li>
    <li><h3>EXPERTISE</h3><p>You have full time access to a highly skilled team at the<br>cost of a paying a part time bookkeeper</p></li>
    <li><h3>FOCUSED STAFF</h3><p>No more office distractions. You focus on your<br>business and we focus on your financials</p></li>
    <li><h3>TECHNOLOGY</h3><p>Outsourcing gives you access to the most current<br>technologies in the industry</p></li>
    <li><h3>EXPERIENCE</h3><p>An outsourced bookkeeper can share specific industry<br>knowledge gained from experience with other clients</p></li>
  </ul>
  <div class="philosophy"></div>
  <h2 class="banner banner--philo">Our Philosophy</h2>
  <ul class="principles">
    <li><span class="icon"><svg viewBox="0 0 30 30"><circle cx="15" cy="15" r="12" fill="none" stroke="#fff" stroke-width="2.5"/><circle cx="15" cy="15" r="6.5" fill="none" stroke="#fff" stroke-width="2.5"/><circle cx="15" cy="15" r="2" fill="#fff"/><path d="M15 15L27 3" stroke="#fff" stroke-width="2"/></svg></span>
      <p><b>ACCURACY.</b> Having accurate and relevant data is the foundation of your financials</p></li>
    <li><span class="icon"><svg viewBox="0 0 30 30"><circle cx="15" cy="13" r="7" fill="none" stroke="#fff" stroke-width="2.5"/><rect x="12" y="21" width="6" height="5" fill="#fff"/><path d="M15 1v3M4 5l2 2M26 5l-2 2M1 13h3M26 13h3" stroke="#fff" stroke-width="2"/></svg></span>
      <p><b>UNDERSTANDING.</b> Knowing what your financials mean to your business</p></li>
    <li><span class="icon"><svg viewBox="0 0 30 30"><circle cx="11" cy="17" r="10" fill="#fff"/><text x="11" y="23" font-size="16" font-weight="700" text-anchor="middle" fill="#1f74ba" font-family="Arial, sans-serif">$</text><circle cx="24" cy="6" r="3" fill="#fff"/><rect x="21.5" y="10" width="5" height="16" rx="2" fill="#fff"/></svg></span>
      <p><b>CONTROL.</b> Taking action based on accurate financials that you understand puts you in control</p></li>
    <li><span class="icon"><svg viewBox="0 0 30 30"><rect x="3" y="13" width="6" height="14" fill="#fff"/><path d="M11 13l5-9c2 0 3 1 3 3l-1 5h8c1.5 0 2.5 1.5 2 3l-3 10c-.3 1-1 2-2 2H11z" fill="#fff"/></svg></span>
      <p><b>ACTION.</b> Results come from taking action</p></li>
  </ul>
  <div class="cta-band">Schedule a Complimentary Consultation TODAY</div>
  <footer class="back-footer">
    <div class="mini-brand"><span></span>HB&amp;C</div>
    <div class="lines">
      <div><svg viewBox="0 0 20 20"><circle cx="10" cy="10" r="9" fill="#2a9bd6"/><circle cx="10" cy="10" r="4" fill="none" stroke="#fff" stroke-width="2"/></svg>484-555-0173</div>
      <div><svg viewBox="0 0 20 20"><circle cx="10" cy="10" r="9" fill="#2a9bd6"/><rect x="5" y="6.5" width="10" height="7" fill="none" stroke="#fff" stroke-width="1.4"/><path d="M5 6.5l5 4 5-4" fill="none" stroke="#fff" stroke-width="1.4"/></svg>erik@halvorsenbooks.com</div>
    </div>
    <div class="place">Maple Valley,<br>PA</div>
  </footer>
</section>

</body>
</html>
```